E learning Platform for privacy

Current website is as below and its more of a shell.
I need someone to take the text and content and design it properly.
https://study.vornaquill.com/

After that, design has to be implemented with elementor and wordpress
https://elementor.com/

```html
<!DOCTYPE html>
<html lang="en">
<head>
<meta charset="utf-8">
<title>Courses – Vornaquill Learning Centre</title>
<link href="https://fonts.googleapis.com/css2?family=Poppins:wght@400;500;600;700&display=swap" rel="stylesheet">
<style>
:root{
  --orange:#f05a22;
  --orange-soft:#fdece5;
  --amber:#f39a1e;
  --ink:#2b2b2b;
  --text:#444;
  --muted:#8a8a8a;
  --line:#e9e9e9;
  --pill:#f1f1f1;
  --green:#1a9c1a;
  --dark:#454545;
  --white:#fff;
}
*{box-sizing:border-box;margin:0;padding:0}
html,body{width:1200px;height:2731px;overflow:hidden}
body{position:relative;background:var(--white);font-family:'Poppins',sans-serif;color:var(--text)}
a{color:inherit;text-decoration:none}

/* header */
.site-header{position:absolute;left:96px;top:0;width:1008px;height:97px;border-bottom:1px solid var(--line)}
.brand{position:absolute;left:0;top:24px}
.brand-name{font-size:30px;font-weight:700;color:var(--orange);letter-spacing:1px;line-height:34px}
.brand-sub{font-size:8px;letter-spacing:6px;color:var(--ink);margin-top:2px;padding-left:10px}
.main-nav{position:absolute;left:364px;top:0;height:97px;display:flex;align-items:center;gap:38px;font-size:12px;font-weight:500;color:var(--ink)}
.main-nav .active{color:var(--amber);position:relative}
.main-nav .active::before{content:"";position:absolute;left:0;right:0;top:-47px;height:3px;background:var(--amber)}
.auth{position:absolute;right:0;top:26px;display:flex;align-items:center;gap:10px;font-size:12px;font-weight:500;color:var(--ink)}
.auth .register{background:var(--pill);border-radius:22px;padding:13px 23px}

/* page head */
.page-title{position:absolute;left:94px;top:128px;font-size:64px;font-weight:700;color:var(--ink);letter-spacing:-0.5px}
.breadcrumb{position:absolute;right:96px;top:160px;font-size:16px;color:var(--ink);display:flex;align-items:center;gap:8px}

/* sidebar */
.sidebar{position:absolute;left:97px;top:247px;width:234px;height:1223px;background:var(--white);border-radius:24px;box-shadow:0 4px 24px rgba(0,0,0,.08);padding:22px 18px 0 18px}
.sidebar h2{font-size:28px;font-weight:600;color:var(--ink);padding-left:5px;padding-bottom:14px;border-bottom:1px solid var(--line)}
.all-courses{font-size:16px;color:var(--ink);padding:14px 5px 16px}
.cat-pill{display:flex;justify-content:space-between;align-items:center;height:40px;background:var(--pill);border-radius:20px;padding:0 18px;font-size:12px;font-weight:500;color:var(--ink);margin-left:2px}
.cat-list{list-style:none;padding:14px 5px 20px;font-size:14px;color:#555}
.cat-list li{height:26.6px}
.sidebar hr{border:0;border-top:1px solid var(--line);margin:0 0 36px}
.gap{height:18px}
.gurus-title{font-size:18px;font-weight:600;color:var(--ink);margin:16px 0 12px}
.guru{display:flex;align-items:center;gap:8px;height:60px;font-size:14px;color:var(--ink)}
.avatar{width:48px;height:48px;border-radius:50%;box-shadow:0 2px 6px rgba(0,0,0,.2);border:2px solid var(--white)}

/* courses */
.course-section{position:absolute;left:357px;width:747px}
.section-head{display:flex;justify-content:space-between;align-items:center;height:40px}
.section-head h2{font-size:28px;font-weight:600;color:var(--ink)}
.pager{display:flex}
.pager span{width:29px;height:29px;border:1px solid #ccc;display:flex;align-items:center;justify-content:center;margin-left:-1px}
.cards{display:flex;gap:21px;margin-top:0}
.card{width:235px;height:376px;background:var(--white);border-radius:12px;box-shadow:0 3px 14px rgba(0,0,0,.07);padding:0 9px;position:relative}
.thumb{height:180px;border-radius:10px;position:relative;top:0}
.card-body{padding:20px 18px 0}
.badge{display:inline-block;background:var(--pill);border-radius:12px;font-size:10px;font-weight:500;color:var(--ink);padding:3px 12px}
.card h3{font-size:16px;font-weight:600;line-height:17px;color:var(--ink);margin-top:10px}
.price{font-size:15px;font-weight:600;color:var(--green);margin-top:10px;line-height:20px}
.meta{font-size:11px;color:var(--muted);display:flex;align-items:center;gap:5px;line-height:14px}
.meta .dot{width:4px;height:4px;border-radius:50%;background:#ccc;margin:0 4px}
.read-more{display:inline-block;margin-top:18px;background:var(--orange-soft);color:var(--orange);font-size:12px;font-weight:500;border-radius:18px;padding:10px 15px}

/* footer */
.footer-shape{position:absolute;left:0;top:2150px}
.newsletter{position:absolute;left:0;width:1200px;top:2280px;text-align:center}
.newsletter h2{font-size:46px;font-weight:600;color:var(--white)}
.subscribe{position:absolute;left:362px;top:2347px;width:464px;height:54px;background:var(--white);border-radius:27px;display:flex;align-items:center;padding:0 12px 0 26px;font-size:14px;color:var(--muted);gap:10px;box-shadow:0 4px 14px rgba(0,0,0,.15)}
.subscribe .send{margin-left:auto;width:36px;height:36px;border-radius:50%;background:var(--orange);display:flex;align-items:center;justify-content:center}
.footer-brand{position:absolute;left:97px;top:2518px;color:var(--white)}
.footer-brand .brand-name{color:var(--white);font-size:34px}
.footer-brand .brand-sub{color:var(--white)}
.footer-col{position:absolute;top:2472px;font-size:14px;color:var(--white)}
.footer-col h4{font-size:15px;font-weight:600;color:#9a9a9a;letter-spacing:.5px;margin-bottom:14px}
.footer-col a{display:block;line-height:27px;padding-left:2px}
.socials{display:flex;gap:9px}
.socials span{width:40px;height:40px;border-radius:50%;background:#5a5a5a;display:flex;align-items:center;justify-content:center}
.socials span i{width:8px;height:8px;border-radius:50%;background:var(--white)}
.footer-rule{position:absolute;left:82px;width:1036px;top:2673px;border-top:1px solid #575757}
.copyright{position:absolute;left:0;width:1200px;top:2694px;text-align:center;font-size:14px;color:var(--white)}
.to-top{position:absolute;left:1129px;top:2655px;width:40px;height:40px;border-radius:50%;background:var(--orange);display:flex;align-items:center;justify-content:center}
</style>
</head>
<body>

<header class="site-header">
  <div class="brand">
    <div class="brand-name">Vornaquill</div>
    <div class="brand-sub">LEARNING CENTRE</div>
  </div>
  <nav class="main-nav">
    <a href="#">HOME</a><a href="#">BLOGS</a><a href="#" class="active">COURSES</a><a href="#">CONTACT US</a><a href="#">ABOUT US</a>
  </nav>
  <div class="auth"><a href="#">SIGN IN</a><a href="#" class="register">REGITER</a></div>
</header>

<h1 class="page-title">Courses</h1>
<div class="breadcrumb">
  <svg width="22" height="20" viewBox="0 0 22 20"><path d="M11 1 1 10h3v9h5v-6h4v6h5v-9h3z" fill="#444"/></svg>
  <span>Home</span><span>|</span><span>Courses</span>
</div>

<aside class="sidebar">
  <h2>Categories</h2>
  <div class="all-courses">All Courses</div>
  <div class="cat-pill">Skyforge Services <span>⌄</span></div>
  <ul class="cat-list">
    <li>› Popular Courses</li><li>› Trending Content</li><li>› Certification Courses</li><li>› Perfect For Beginners</li><li>› Intermediate Courses</li><li>› Advanced Courses</li>
  </ul>
  <hr>
  <div class="cat-pill">Nimbus Cloud <span>⌄</span></div>
  <ul class="cat-list">
    <li>› Certification Courses</li><li>› Popular Courses</li><li>› Trending Content</li><li>› Perfect For Beginners</li><li>› Intermediate Courses</li><li>› Advanced Courses</li>
  </ul>
  <hr>
  <div class="cat-pill">Stratus Cloud <span>›</span></div>
  <div class="gap"></div>
  <div class="cat-pill">Kernel Cloud <span>›</span></div>
  <div class="gap"></div>
  <hr style="margin-bottom:0">
  <div class="gurus-title" style="margin-top:38px">Top Gurus</div>
  <div class="guru"><span class="avatar" role="img" aria-label="Portrait of instructor" style="background:#7a5a3a"></span>Ravi Kellner</div>
  <div class="guru"><span class="avatar" role="img" aria-label="Portrait of instructor" style="background:#3e4a55"></span>Niko Tarrant</div>
  <div class="guru"><span class="avatar" role="img" aria-label="Portrait of instructor" style="background:#d9455f"></span>Sean Pelham</div>
  <div class="guru"><span class="avatar" role="img" aria-label="Portrait of instructor" style="background:#3fb7c0"></span>Bram Tolley</div>
  <div class="guru"><span class="avatar" role="img" aria-label="Portrait of instructor" style="background:#b89a84"></span>Fiona Ellery</div>
</aside>

<!-- card template repeated per section -->
<section class="course-section" style="top:242px">
  <div class="section-head"><h2>Popular Courses</h2><div class="pager"><span>‹</span><span>›</span></div></div>
  <div class="cards" style="margin-top:16px">
    <article class="card"><div class="thumb" role="img" aria-label="Abstract purple background artwork" style="background:linear-gradient(135deg,#8a1f6a,#4a0f4a)"></div><div class="card-body"><span class="badge">FEATURED</span><h3>Opalis Demonstration Course</h3><div class="price">FREE</div><div class="meta">▦ Dec 19, 2020<span class="dot"></span>● Mr Example</div><a class="read-more" href="#">READ MORE</a></div></article>
    <article class="card"><div class="thumb" role="img" aria-label="Blue gradient geometric artwork" style="background:linear-gradient(135deg,#1a5fe0,#12b2f0)"></div><div class="card-body"><span class="badge">FEATURED</span><h3>Opalis Demonstration Course</h3><div class="price">FREE</div><div class="meta">▦ Dec 19, 2020<span class="dot"></span>● Mr Example</div><a class="read-more" href="#">READ MORE</a></div></article>
    <article class="card"><div class="thumb" role="img" aria-label="Yellow sunburst artwork" style="background:radial-gradient(circle,#fff6a0,#f6c800 70%)"></div><div class="card-body"><span class="badge">FEATURED</span><h3>Opalis Demonstration Course</h3><div class="price">FREE</div><div class="meta">▦ Dec 19, 2020<span class="dot"></span>● Mr Example</div><a class="read-more" href="#">READ MORE</a></div></article>
  </div>
</section>

<section class="course-section" style="top:710px">
  <div class="section-head"><h2>Trending Content</h2><div class="pager"><span>‹</span><span>›</span></div></div>
  <div class="cards" style="margin-top:16px">
    <article class="card"><div class="thumb" role="img" aria-label="Orange wave artwork" style="background:linear-gradient(135deg,#f57e3a,#f6b640 50%,#ef5d55)"></div><div class="card-body"><span class="badge">FEATURED</span><h3>Opalis Demonstration Course</h3><div class="price">FREE</div><div class="meta">▦ Dec 19, 2020<span class="dot"></span>● Mr Example</div><a class="read-more" href="#">READ MORE</a></div></article>
    <article class="card"><div class="thumb" role="img" aria-label="Futuristic blue and pink artwork" style="background:linear-gradient(160deg,#0f3a9c,#1a1e5a 55%,#e0306a)"></div><div class="card-body"><span class="badge">FEATURED</span><h3>Opalis Demonstration Course</h3><div class="price">FREE</div><div class="meta">▦ Dec 19, 2020<span class="dot"></span>● Mr Example</div><a class="read-more" href="#">READ MORE</a></div></article>
    <article class="card"><div class="thumb" role="img" aria-label="Colourful event poster artwork" style="background:linear-gradient(135deg,#f6702a,#e8306a 50%,#4a6ee8)"></div><div class="card-body"><span class="badge">FEATURED</span><h3>Opalis Demonstration Course</h3><div class="price">FREE</div><div class="meta">▦ Dec 19, 2020<span class="dot"></span>● Mr Example</div><a class="read-more" href="#">READ MORE</a></div></article>
  </div>
</section>

<section class="course-section" style="top:1176px">
  <div class="section-head"><h2>Certification Courses</h2><div class="pager"><span>‹</span><span>›</span></div></div>
  <div class="cards" style="margin-top:14px">
    <article class="card"><div class="thumb" role="img" aria-label="Modern pink and purple artwork" style="background:linear-gradient(135deg,#e8164a,#8a2aa8 70%,#5a1a9a)"></div><div class="card-body"><span class="badge">FEATURED</span><h3>Opalis Demonstration Course</h3><div class="price">FREE</div><div class="meta">▦ Dec 19, 2020<span class="dot"></span>● Mr Example</div><a class="read-more" href="#">READ MORE</a></div></article>
    <article class="card"><div class="thumb" role="img" aria-label="Festive bokeh artwork" style="background:radial-gradient(circle at 40% 40%,#c4a44a,#4a6a4a 60%,#1f3a3e)"></div><div class="card-body"><span class="badge">FEATURED</span><h3>Opalis Demonstration Course</h3><div class="price">FREE</div><div class="meta">▦ Dec 19, 2020<span class="dot"></span>● Mr Example</div><a class="read-more" href="#">READ MORE</a></div></article>
    <article class="card"><div class="thumb" role="img" aria-label="Dark teal geometric artwork" style="background:radial-gradient(circle,#2a4a4e,#152426)"></div><div class="card-body"><span class="badge">FEATURED</span><h3>Opalis Demonstration Course</h3><div class="price">FREE</div><div class="meta">▦ Dec 19, 2020<span class="dot"></span>● Mr Example</div><a class="read-more" href="#">READ MORE</a></div></article>
  </div>
</section>

<section class="course-section" style="top:1642px">
  <div class="section-head"><h2>Advanced</h2><div class="pager"><span>‹</span><span>›</span></div></div>
  <div class="cards" style="margin-top:14px">
    <article class="card"><div class="thumb" role="img" aria-label="Dark green sale artwork" style="background:radial-gradient(circle,#1f4a3a,#111a22 70%)"></div><div class="card-body"><span class="badge">FEATURED</span><h3>Opalis Demonstration Course</h3><div class="price">FREE</div><div class="meta">▦ Dec 19, 2020<span class="dot"></span>● Mr Example</div><a class="read-more" href="#">READ MORE</a></div></article>
    <article class="card"><div class="thumb" role="img" aria-label="Orange and pink fluid artwork" style="background:linear-gradient(135deg,#f6902a,#f0503a 50%,#e8307a)"></div><div class="card-body"><span class="badge">FEATURED</span><h3>Opalis Demonstration Course</h3><div class="price">FREE</div><div class="meta">▦ Dec 19, 2020<span class="dot"></span>● Mr Example</div><a class="read-more" href="#">READ MORE</a></div></article>
    <article class="card"><div class="thumb" role="img" aria-label="Dark and orange abstract artwork" style="background:linear-gradient(170deg,#f06a1a 0 12%,#2a2a2a 12% 86%,#f06a1a 86%)"></div><div class="card-body"><span class="badge">FEATURED</span><h3>Opalis Demonstration Course</h3><div class="price">FREE</div><div class="meta">▦ Dec 19, 2020<span class="dot"></span>● Mr Example</div><a class="read-more" href="#">READ MORE</a></div></article>
  </div>
</section>

<footer>
  <svg class="footer-shape" width="1200" height="581" viewBox="0 0 1200 581">
    <path d="M0 219 C 250 60 450 31 600 31 C 820 31 1050 100 1200 182 L1200 581 L0 581 Z" fill="#f2921e"/>
    <path d="M0 230 C 250 100 450 76 620 76 C 860 76 1060 190 1200 277 L1200 581 L0 581 Z" fill="var(--dark)"/>
  </svg>
  <div class="newsletter"><h2>Newsletter</h2></div>
  <div class="subscribe">
    <svg width="18" height="14" viewBox="0 0 18 14"><rect x="1" y="1" width="16" height="12" rx="1" fill="none" stroke="#999"/><path d="M1 1l8 6 8-6" fill="none" stroke="#999"/></svg>
    Enter your email address
    <span class="send"><svg width="16" height="16" viewBox="0 0 16 16"><path d="M15 1 1 7l5 2 2 5z" fill="#fff"/></svg></span>
  </div>
  <div class="footer-brand">
    <div class="brand-name">Vornaquill</div>
    <div class="brand-sub">LEARNING CENTRE</div>
  </div>
  <div class="footer-col" style="left:399px"><h4>COMPANY</h4><a href="#">About</a><a href="#">Courses</a><a href="#">FAQs</a></div>
  <div class="footer-col" style="left:557px"><h4>GET INVOLVED</h4><a href="#">Blog</a><a href="#">Contact</a></div>
  <div class="footer-col" style="left:728px"><h4>INFORMATION</h4><a href="#">Terms of Service</a><a href="#">Honor Code</a><a href="#">Privacy Policy</a></div>
  <div class="footer-col" style="left:914px"><h4>FOLLOW US</h4>
    <div class="socials">
      <span aria-label="Social profile 1"><i></i></span><span aria-label="Social profile 2"><i></i></span><span aria-label="Social profile 3"><i></i></span><span aria-label="Social profile 4"><i></i></span>
    </div>
  </div>
  <div class="footer-rule"></div>
  <div class="copyright">© Copyright Vornaquill 2020. All rights reserved.</div>
  <a class="to-top" href="#" aria-label="Back to top"><svg width="14" height="16" viewBox="0 0 14 16"><path d="M7 15V2M2 7l5-5 5 5" fill="none" stroke="#fff" stroke-width="1.6"/></svg></a>
</footer>

</body>
</html>
```